Larkhollow needs a Webpage Design

We need a webpage for Dr. XYZ who is doing consultancy practice in the area of speech, language, and reading disabilities. He is doing his consultancy practice as "Larkhollow Consultants". Our target market is clients with annual income of $100,000 or more in Chicago area. Our business philosophy is: "...We provide the best evidence-based services/interventions, at an affordable fee, and deal only with clients who seek such services...."

Dr. XYZ's area of research interests are: a) using assistive technology for communication for children with autism, b) early intervention with focus on parent participation, and c) language learning for children birth-to-five years.

He works at a public university whose school color is 'Orange". Home page should show two logos (university and practice). Each page should stand on its own and reflect the content with minimal scrolling. The colors should be subdued (not bright colors) to attract college educated wealthy individuals who are seeking best evidence-based practice in speech, language, and reading for their children.

We need five pages: Home, Consultation, Research, Professional Development, and Contact (with google map directions). The home page should have space for a picture and links for facebook, twitter, and google plus. Other pages should have space for at least one picture and links to pdf files.

The overall design should show healthcare service, evidence-based early intervention with focus on parent participation, and project that we are leaders in the field.

```html
<!DOCTYPE html>
<html lang="en">
<head>
<meta charset="utf-8">
<title>Larkhollow Consultants – Professional Development</title>
<link rel="stylesheet" href="https://fonts.googleapis.com/css2?family=Open+Sans:wght@400;600&family=Bebas+Neue&display=swap">
<style>
:root{
  --blue:#1672bd;
  --blue-dark:#0f5f9f;
  --green:#45c22e;
  --header-bg:#eeeeee;
  --text:#6f6f6f;
  --text-dark:#555;
  --cal-dark:#3a3a3a;
  --cal-cell:#e4e4e4;
  --cal-line:#c9c9c9;
  --cal-today:#6fb3c9;
  --photo-a:#f3ede6;
  --photo-b:#d9c3a8;
  --social:#5f6a66;
}
*{margin:0;padding:0;box-sizing:border-box}
html,body{width:991px;height:1200px;overflow:hidden}
body{position:relative;background:#fff;font-family:"Open Sans",Arial,sans-serif;color:var(--text)}
.abs{position:absolute}

.top-bar{left:0;top:0;width:991px;height:15px;background:var(--blue)}
.search{left:742px;top:1px;width:104px;height:13px;background:#fff;font-size:8px;color:#333;padding:1px 4px;display:flex;justify-content:space-between;align-items:center}

.site-header{left:0;top:15px;width:991px;height:139px;background:var(--header-bg);border-bottom:1px solid #d6d6d6}
.brand{left:128px;top:54px;display:flex;align-items:center;gap:8px;font-size:19px;font-weight:600;color:var(--blue)}
.brand-mark{width:24px;height:24px;background:var(--blue)}
.doctor{left:458px;top:42px;color:#6b6b6b}
.doctor-name{font-size:24px;line-height:28px}
.doctor-name small{font-size:14px;color:#8a8a8a;margin-left:6px}
.doctor-title{font-size:12.5px;color:#7a7a7a}
.contact-line{left:128px;width:155px;font-size:14.5px;color:#6b6b6b;display:flex;align-items:center;gap:7px;white-space:nowrap}

.main-nav{left:290px;top:119px;height:35px;display:flex;gap:2px}
.nav-tab{position:relative;height:35px;padding:12px 4px 0;font-family:Arial,"Open Sans",sans-serif;font-size:12.5px;color:#fff;border-radius:6px 6px 0 0;text-align:center;white-space:nowrap}
.nav-tab::after{content:"+";position:absolute;right:6px;top:-3px;font-size:11px}
.nav-blue{background:var(--blue)}
.nav-green{background:var(--green)}

.hero-photo{left:128px;top:166px;width:485px;height:317px;background:linear-gradient(135deg,var(--photo-a) 0%,#efe2d3 55%,var(--photo-b) 100%)}

.calendar{left:630px;top:166px;width:209px;box-shadow:0 1px 3px rgba(0,0,0,.3);background:var(--cal-cell)}
.cal-head{height:36px;background:var(--cal-dark);color:#fff;display:flex;align-items:center;justify-content:space-between;padding:0 10px;font-size:14px;font-weight:600}
.cal-table{width:100%;border-collapse:collapse;table-layout:fixed}
.cal-table th{height:16px;font-size:7.5px;font-weight:600;color:#555;background:#ececec}
.cal-table td{height:30px;text-align:center;font-size:12px;color:#444;border:1px solid var(--cal-line)}
.cal-table td.muted{color:#aaa;background:#efefef}
.cal-table td.today{background:var(--cal-today);color:#2e6a80}

.news-title{left:631px;top:414px;display:flex;align-items:center;gap:9px;font-family:"Bebas Neue",Impact,sans-serif;font-size:17px;color:var(--blue);letter-spacing:.3px}
.news-item{left:635px;width:205px;font-size:10px;line-height:15px;color:#666}
.news-meta{display:flex;align-items:center;gap:4px;font-size:10.5px}
.news-meta svg{flex:none}
.divider{left:631px;top:640px;width:233px;height:1px;background:#ccc}
.pdf-button{left:670px;top:664px;width:154px;height:58px;background:var(--blue);padding:6px;box-shadow:0 1px 2px rgba(0,0,0,.3)}
.pdf-button span{display:flex;align-items:center;justify-content:center;gap:8px;height:100%;border:1px solid #b9d6ef;color:#fff;font-size:15px;letter-spacing:1px}

.social-rail{left:963px;top:260px;width:28px;height:135px;background:var(--social);padding:4px 4px;display:flex;flex-direction:column;gap:4px}
.social-rail i{display:block;width:18px;height:18px;background:#d9dcdb;margin-left:1px}

.page-title{left:128px;top:524px;font-family:"Bebas Neue",Impact,sans-serif;font-weight:400;font-size:28px;color:var(--blue);letter-spacing:1px}
.title-stripes{left:441px;top:528px;width:172px;height:14px;background:repeating-linear-gradient(180deg,#b7d3ec 0 2px,#e3eef8 2px 4px)}
.body-copy{left:128px;width:486px;font-size:11.6px;line-height:17.5px;color:var(--text)}
.bullets{left:128px;top:724px;list-style:none;font-size:11.6px;color:var(--text)}
.bullets li{display:flex;align-items:center;gap:12px;height:36px}
.bullets li::before{content:"";width:13px;height:13px;border-radius:50%;background:var(--blue)}

.site-footer{left:0;top:1068px;width:991px;height:105px;background:var(--blue)}
.uni-badge{left:128px;top:1090px;width:52px;height:52px;background:#1a1a1a;border-radius:50%}
.footer-brand{left:211px;top:1106px;display:flex;align-items:center;gap:6px;font-size:13px;font-weight:600;color:#c9dcec}
.footer-brand i{width:14px;height:14px;background:#c9dcec}
.footer-address{left:433px;top:1093px;font-size:11.6px;line-height:13.5px;color:#d6e6f3}
.footer-contact{left:693px;top:1094px;color:#fff}
.footer-contact h3{font-family:"Bebas Neue",Impact,sans-serif;font-weight:400;font-size:17px;letter-spacing:.5px;display:flex;align-items:center;gap:6px;margin-bottom:8px}
.footer-contact p{font-size:11.5px;color:#dbe8f3;display:flex;align-items:center;gap:9px;line-height:20px}
.bottom-bar{left:0;top:1173px;width:991px;height:27px;background:var(--green);font-size:10px;color:#1d3a12}
.bottom-bar span{position:absolute;top:8px}
</style>
</head>
<body>

<div class="abs top-bar"></div>
<div class="abs search"><span>Search...</span>
  <svg width="8" height="8" viewBox="0 0 10 10"><circle cx="4" cy="4" r="3" fill="none" stroke="#555" stroke-width="1.4"/><line x1="6.2" y1="6.2" x2="9.3" y2="9.3" stroke="#555" stroke-width="1.5"/></svg>
</div>

<header class="abs site-header"></header>
<div class="abs brand"><i class="brand-mark"></i>Larkhollow Consultants</div>
<div class="abs doctor">
  <div class="doctor-name">Dr.XYZ<small>Ph.D. CCC-SLP</small></div>
  <div class="doctor-title">Speech-Language Pathologist</div>
</div>
<div class="abs contact-line" style="top:111px">
  <svg width="12" height="9" viewBox="0 0 12 9"><rect width="12" height="9" fill="#6b6b6b"/><path d="M0 0l6 5 6-5" fill="none" stroke="#eee" stroke-width="1.2"/></svg>
  info@larkco.com
</div>
<div class="abs contact-line" style="top:131px">
  <svg width="12" height="12" viewBox="0 0 12 12"><path d="M3 1l2 3-1.3 1.2a7 7 0 0 0 3 3L8 7l3 2-1 2C5 11 1 7 1 2z" fill="#6b6b6b"/></svg>
  +100 555 014
</div>

<nav class="abs main-nav">
  <div class="nav-tab nav-blue" style="width:79px">HOME</div>
  <div class="nav-tab nav-green" style="width:110px">CONSULTATION</div>
  <div class="nav-tab nav-blue" style="width:90px">RESEARCH</div>
  <div class="nav-tab nav-green" style="width:193px">PROFESSIONAL DEVELOPMENT</div>
  <div class="nav-tab nav-blue" style="width:83px">CONTACT</div>
</nav>

<div class="abs hero-photo" role="img" aria-label="Photo of a child building a small brick house from toy blocks on a white table"></div>

<aside class="abs calendar">
  <div class="cal-head"><span>&#9664;</span><span>JUL 2014</span><span>&#9654;</span></div>
  <table class="cal-table">
    <tr><th>MON</th><th>TUE</th><th>WED</th><th>THU</th><th>FRI</th><th>SAT</th><th>SUN</th></tr>
    <tr><td class="muted">30</td><td>1</td><td class="today">2</td><td>3</td><td>4</td><td>5</td><td>6</td></tr>
    <tr><td>7</td><td>8</td><td>9</td><td>10</td><td>11</td><td>12</td><td>13</td></tr>
    <tr><td>14</td><td>15</td><td>16</td><td>17</td><td>18</td><td>19</td><td>20</td></tr>
    <tr><td>21</td><td>22</td><td>23</td><td>24</td><td>25</td><td>26</td><td>27</td></tr>
    <tr><td>28</td><td>29</td><td>30</td><td>31</td><td class="muted">1</td><td class="muted">2</td><td class="muted">3</td></tr>
  </table>
</aside>

<div class="abs news-title">
  <svg width="16" height="14" viewBox="0 0 16 14"><path d="M0 0h16v10H6l-4 4v-4H0z" fill="var(--green)"/></svg>
  LATEST NEWS
</div>
<div class="abs news-item" style="top:444px">
  <div class="news-meta"><svg width="10" height="10" viewBox="0 0 10 10"><circle cx="5" cy="5" r="4.2" fill="none" stroke="#999" stroke-width="1.2"/><path d="M5 2.5V5h2" fill="none" stroke="#999"/></svg>17 Jun 2014 <svg width="11" height="9" viewBox="0 0 11 9"><ellipse cx="5.5" cy="4" rx="5.5" ry="4" fill="#999"/></svg>100 comments</div>
  Autism symptoms 'reversed' in mice by 100-year-old drug.
</div>
<div class="abs news-item" style="top:501px">
  <div class="news-meta"><svg width="10" height="10" viewBox="0 0 10 10"><circle cx="5" cy="5" r="4.2" fill="none" stroke="#999" stroke-width="1.2"/><path d="M5 2.5V5h2" fill="none" stroke="#999"/></svg>20 Jun 2014 <svg width="11" height="9" viewBox="0 0 11 9"><ellipse cx="5.5" cy="4" rx="5.5" ry="4" fill="#999"/></svg>80 comments</div>
  Autism link discovered in brains of mice with 'mohawks'.
</div>
<div class="abs news-item" style="top:558px">
  <div class="news-meta"><svg width="10" height="10" viewBox="0 0 10 10"><circle cx="5" cy="5" r="4.2" fill="none" stroke="#999" stroke-width="1.2"/><path d="M5 2.5V5h2" fill="none" stroke="#999"/></svg>15 Jun 2014 <svg width="11" height="9" viewBox="0 0 11 9"><ellipse cx="5.5" cy="4" rx="5.5" ry="4" fill="#999"/></svg>40 comments</div>
  Children with autism have mitochondrial deficits.
</div>
<div class="abs divider"></div>
<a class="abs pdf-button"><span>
  <svg width="14" height="14" viewBox="0 0 14 14"><g fill="none" stroke="#fff" stroke-width="2"><rect x="1" y="6" width="7" height="4" rx="2" transform="rotate(-45 4.5 8)"/><rect x="6" y="4" width="7" height="4" rx="2" transform="rotate(-45 9.5 6)"/></g></svg>
  LINK TO PDF</span></a>

<div class="abs social-rail" aria-label="Social links"><i></i><i></i><i></i><i></i><i></i><i></i></div>

<h1 class="abs page-title">PROFESSIONAL DEVELOPMENT</h1>
<div class="abs title-stripes"></div>
<p class="abs body-copy" style="top:569px">Nam libero tempore, cum soluta nobis est eligendi optio cumque nihil impedit quo minus id quod maxime placeat facere possimus, omnis voluptas assumenda est, omnis dolor repellendus.</p>
<p class="abs body-copy" style="top:637px">Temporibus autem quibusdam et aut officiis debitis aut rerum necessitatibus saepe eveniet ut et voluptates repudiandae sint et molestiae non recusandae. Itaque earum rerum hic tenetur a sapiente delectus, ut aut reiciendis voluptatibus maiores alias consequatur aut perferendis doloribus asperiores repellat.</p>
<ul class="abs bullets">
  <li>Tempora incidunt ut labore et dolore magnam aliquam quaerat.</li>
  <li>Exercitationem ullam corporis suscipit laboriosam.</li>
  <li>Excepteur sint occaecat cupidatat non proident.</li>
  <li>Duis aute irure dolor in reprehenderit in voluptate.</li>
  <li>Sunt in culpa qui officia deserunt mollit anim.</li>
</ul>
<p class="abs body-copy" style="top:942px">Neque porro quisquam est, qui dolorem ipsum quia dolor sit amet, consectetur, adipisci velit, sed quia non numquam eius modi tempora incidunt ut labore et dolore magnam aliquam quaerat voluptatem.</p>

<footer class="abs site-footer"></footer>
<div class="abs uni-badge" role="img" aria-label="Harlan Ridge University badge"></div>
<div class="abs footer-brand"><i></i>Larkhollow</div>
<div class="abs footer-address">Dr. XYZ, Ph.D.<br>Associate Professor<br>Department of ABC<br>College of yadi yadi yada</div>
<div class="abs footer-contact">
  <h3><svg width="12" height="9" viewBox="0 0 12 9"><rect width="12" height="9" fill="#fff"/><path d="M0 0l6 5 6-5" fill="none" stroke="var(--blue)" stroke-width="1.2"/></svg>CONTACT US</h3>
  <p><svg width="11" height="8" viewBox="0 0 12 9"><rect width="12" height="9" fill="#fff"/><path d="M0 0l6 5 6-5" fill="none" stroke="var(--blue)" stroke-width="1.2"/></svg>info@larkco.com</p>
  <p><svg width="11" height="11" viewBox="0 0 12 12"><path d="M3 1l2 3-1.3 1.2a7 7 0 0 0 3 3L8 7l3 2-1 2C5 11 1 7 1 2z" fill="#fff"/></svg>+ 100 555 014</p>
</div>
<div class="abs bottom-bar">
  <span style="left:128px">copyright information here</span>
  <span style="left:297px">Home</span>
  <span style="left:341px">Consultation</span>
  <span style="left:411px">Research</span>
  <span style="left:473px">Site Map</span>
  <span style="left:813px">Back to top</span>
</div>

</body>
</html>
```